Design 4 pages for an event discovery website

This is a contest for the design of 4 pages for an events discovery website. The feature is part of the new sign-up process.

Please see the attached document for a full scope, mockups and the parent category icons.

Target Market(s)

18-35 Australian event goers

Industry/Entity Type

Events

Number of Pages Required

4 page

```html
<!DOCTYPE html>
<html lang="en">
<head>
<meta charset="utf-8">
<title>gathera – Link your accounts</title>
<link href="https://fonts.googleapis.com/css2?family=Lato:wght@300;400;700;900&display=swap" rel="stylesheet">
<style>
  :root{
    --brand-green:#0e9a78;
    --lime:#9cc92b;
    --lime-dark:#6f9a12;
    --sky:#3fb8ee;
    --sky-dark:#1e8fc4;
    --navy:#1f3152;
    --navy-dark:#121e35;
    --charcoal:#2a2a2a;
    --charcoal-dark:#161616;
    --header-bg:#ebebeb;
    --footer-bg:#ededed;
    --ink:#333;
    --white:#fff;
  }
  *{box-sizing:border-box;margin:0;padding:0}
  html,body{width:1200px;height:785px;overflow:hidden}
  body{font-family:'Lato',sans-serif;background:var(--header-bg);position:relative}

  .site-header{position:absolute;left:0;top:0;width:1200px;height:80px;background:var(--header-bg)}
  .brand{position:absolute;left:111px;top:18px;font-size:38px;font-weight:900;color:var(--brand-green);line-height:1;letter-spacing:-0.5px}
  .nav-link{position:absolute;left:354px;top:32px;font-size:14px;color:var(--ink)}
  .search{position:absolute;left:608px;top:22px;width:262px;height:35px;background:var(--white);border-radius:7px;padding:0 10px;line-height:35px;font-size:15px;color:#999;font-weight:300}
  .btn{position:absolute;top:22px;width:100px;height:35px;border-radius:7px;color:var(--white);font-size:17px;font-weight:700;text-align:center;line-height:35px}
  .btn-signup{left:881px;background:var(--brand-green)}
  .btn-login{left:990px;background:var(--lime)}

  .hero{position:absolute;left:0;top:80px;width:1200px;height:625px;
    background:
      radial-gradient(ellipse 380px 220px at 800px 330px, rgba(120,90,150,.55), transparent 70%),
      radial-gradient(ellipse 500px 300px at 250px 200px, rgba(110,70,35,.55), transparent 75%),
      linear-gradient(180deg,#2a1c16 0%,#1c1512 50%,#0d0909 100%);}
  .hero-content{position:absolute;left:0;top:0;width:100%;height:100%;color:var(--white)}
  .step-title{position:absolute;left:130px;top:106px;font-size:27px;font-weight:700}
  .point{position:absolute;left:131px;display:flex;align-items:center;font-size:15.5px;font-weight:300}
  .point svg{margin-right:26px}
  .point-1{top:170px}
  .point-2{top:228px}

  .service{position:absolute;left:134px;width:241px;height:50px;border-radius:5px;display:flex;align-items:center;color:var(--white);font-size:19px;font-weight:700}
  .service .icon-cell{width:43px;height:100%;display:flex;align-items:center;justify-content:center;border-right:1px solid rgba(0,0,0,.18)}
  .service .label{padding-left:14px}
  .service-chirp{top:282px;background:linear-gradient(#55c8f6,var(--sky));box-shadow:0 4px 0 var(--sky-dark)}
  .service-snap{top:345px;background:linear-gradient(#2a3e63,var(--navy-dark));box-shadow:0 3px 0 #0b1322}
  .service-sound{top:409px;background:linear-gradient(#b4dc4a,var(--lime));box-shadow:0 4px 0 var(--lime-dark)}
  .service-tune{top:472px;background:linear-gradient(#333,var(--charcoal-dark));box-shadow:0 3px 0 #0a0a0a}
  .status{position:absolute;left:402px;font-size:12px}
  .status-linked{top:302px}
  .status-note{top:427px}

  .site-footer{position:absolute;left:0;top:705px;width:1200px;height:80px;background:var(--footer-bg);font-size:12.5px;color:var(--ink)}
  .copyright{position:absolute;left:0;width:100%;top:32px;text-align:center}
  .page-code{position:absolute;left:1156px;top:32px}
</style>
</head>
<body>
  <header class="site-header">
    <div class="brand">gathera</div>
    <a class="nav-link">Find Events</a>
    <div class="search">Search</div>
    <div class="btn btn-signup">Sign Up</div>
    <div class="btn btn-login">Login</div>
  </header>

  <section class="hero">
    <div class="hero-bg" role="img" aria-label="Photo of a packed theatre audience facing a lit stage" style="position:absolute;inset:0"></div>
    <div class="hero-content">
      <h1 class="step-title">Step 1 to 5</h1>
      <p class="point point-1">
        <svg width="14" height="14" viewBox="0 0 14 14"><rect width="14" height="14" rx="2" fill="#9cc92b"/><path d="M3.5 7.2l2.4 2.4 4.6-4.8" stroke="#1d2a08" stroke-width="1.8" fill="none"/></svg>
        Link to other social media accounts and media players
      </p>
      <p class="point point-2">
        <svg width="14" height="14" viewBox="0 0 14 14"><rect width="14" height="14" rx="2" fill="#9cc92b"/><path d="M3.5 7.2l2.4 2.4 4.6-4.8" stroke="#1d2a08" stroke-width="1.8" fill="none"/></svg>
        By linking your accounts,we can save a you a lot of time by automatically&nbsp; determining your interests
      </p>

      <div class="service service-chirp"><span class="icon-cell"><svg width="16" height="16"><circle cx="8" cy="8" r="7" fill="#fff"/></svg></span><span class="label">Chirpline</span></div>
      <div class="service service-snap"><span class="icon-cell"><svg width="16" height="16"><rect x="1" y="1" width="14" height="14" rx="2" fill="#fff"/></svg></span><span class="label">Snapframe</span></div>
      <div class="service service-sound"><span class="icon-cell"><svg width="16" height="16"><circle cx="8" cy="8" r="7" fill="#fff"/></svg></span><span class="label">Soundloop</span></div>
      <div class="service service-tune"><span class="icon-cell"><svg width="16" height="16"><circle cx="8" cy="8" r="7" fill="#fff"/></svg></span><span class="label">Tunevault</span></div>

      <span class="status status-linked">Linked</span>
      <span class="status status-note">We dont have that feature yet but have regarded your interest</span>
    </div>
  </section>

  <footer class="site-footer">
    <p class="copyright">© 2015 Company&nbsp; Name , All Rights Reserved</p>
    <span class="page-code">C5</span>
  </footer>
</body>
</html>
```